e-commerce store for sport clothing online store "baseball merchandise "web application...

I want to design a UX/UI for my web application website for the online store I will provide you with the following:
1. screen shots of the initial design for the pages>
2. the logo files.
3. The brand guideline file.

the provided files (screen shots) is guideline I want to see CREATIVITY with the UX/UI DESIGN.
PS. PLEASE FOLLOW THE BRANDGUIDE LINE CAREFULLY SPECIALLY THE TYPOGRAPHY & THE COLOR CODES.

PLEASE VISIT THIS WEBSITE brightlane.varomi-qz.com to see more for the screens.

```html
<!DOCTYPE html>
<html lang="en">
<head>
<meta charset="utf-8">
<title>Basepath Store – Home and Checkout</title>
<link href="https://fonts.googleapis.com/css2?family=Barlow+Condensed:wght@400;500;600;700&display=swap" rel="stylesheet">
<style>
:root{
  --olive:#9a8c61;
  --red:#a5102c;
  --navy:#1d2747;
  --ink:#1a1a1a;
  --muted:#8a8a8a;
  --bg:#e8e8e8;
  --white:#ffffff;
  --line:#9d9d9d;
  --feature:#d7e3f5;
}
*{box-sizing:border-box;margin:0;padding:0}
html,body{width:911px;height:1200px;overflow:hidden;background:var(--white)}
body{font-family:"Barlow Condensed",sans-serif;color:var(--ink)}
.canvas{position:relative;width:911px;height:1200px;overflow:hidden}
.stage{position:absolute;left:0;top:0;width:1500px;height:1976px;transform:scale(0.6073);transform-origin:0 0}
.abs{position:absolute}
.screen{position:absolute;left:50px;width:1400px;height:862px;background:var(--bg);box-shadow:0 2px 6px rgba(0,0,0,.12)}
.screen--home{top:60px}
.screen--checkout{top:1001px}
.sidebar{position:absolute;left:0;top:0;width:150px;height:100%;background:var(--white)}
.topbar{position:absolute;left:150px;top:0;width:1250px;height:70px;background:var(--olive);border-bottom-right-radius:22px}
.brand{position:absolute;left:22px;top:30px;display:flex;align-items:center;gap:6px;font-weight:700;font-size:27px;color:var(--navy);letter-spacing:.5px}
.brand i{width:12px;height:12px;border-radius:50%;background:var(--red);display:block}
.nav-item{position:absolute;left:0;width:150px;height:48px;display:flex;align-items:center;justify-content:center;gap:14px;color:var(--navy)}
.nav-item.is-active{background:#efefef;color:var(--red);font-size:24px;font-weight:500}
.nav-item svg{width:34px;height:34px}
.search{position:absolute;left:593px;top:14px;width:330px;height:40px;background:var(--white);border-radius:6px;display:flex;align-items:center;padding-left:16px;gap:18px;font-size:24px;color:#777}
.search svg{width:22px;height:22px}
.icon{position:absolute}
.badge{position:absolute;width:16px;height:16px;border-radius:50%;background:var(--navy);color:#fff;font-size:12px;display:flex;align-items:center;justify-content:center;font-weight:600}
.photo{position:absolute;border-radius:8px}
.photo--banner{left:164px;top:104px;width:913px;height:193px;background:linear-gradient(100deg,#c94a4f 0%,#d8d3d3 45%,#b6b6b8 60%,#c5383e 100%)}
.photo--side{left:1106px;top:104px;width:260px;height:273px;background:radial-gradient(circle at 60% 40%,#4e79b5 0%,#1c3a6b 55%,#0e1f3d 100%)}
.dropdown{position:absolute;left:164px;top:319px;width:913px;height:52px;background:var(--olive);border-radius:8px;color:#fff;font-size:30px;padding-left:36px;display:flex;align-items:center}
.dropdown svg{position:absolute;right:26px;top:15px;width:26px;height:22px}
.card{position:absolute;background:var(--white);border-radius:6px;text-align:center}
.card--home{top:390px;width:290px;height:358px}
.prod{position:absolute;left:50%;transform:translateX(-50%);border-radius:40px 40px 14px 14px}
.prod--cap{background:linear-gradient(180deg,#3a3a58,#1f1f35)}
.prod--tee{background:linear-gradient(180deg,#ececec,#c9c9c9);border-radius:16px 16px 6px 6px}
.prod--hat{background:radial-gradient(circle,#8fb0cf,#35608e);border-radius:50%}
.card-title{position:absolute;left:0;right:0;font-size:27px;font-weight:500}
.card-desc{position:absolute;left:18px;right:18px;font-size:15px;line-height:20px;font-weight:500}
.price{position:absolute;background:var(--red);color:#fff;border-radius:6px;display:flex;align-items:center;justify-content:center;font-weight:600}
.card--home .price{left:15px;right:16px;top:288px;height:49px;font-size:30px}
.pager{position:absolute;width:40px;height:40px;border-radius:50%;background:#fff;display:flex;align-items:center;justify-content:center}
.pager svg{width:16px;height:18px}
.panel-title{position:absolute;font-size:23px;font-weight:500;display:flex;align-items:center;gap:10px}
.rule{position:absolute;height:1px;background:var(--line)}
.thumb{position:absolute;width:60px;height:60px;background:#fff;border-radius:6px}
.thumb span{position:absolute;left:12px;top:8px;width:36px;height:44px}
.mini-name{position:absolute;font-size:15px;font-weight:500;white-space:nowrap}
.mini-price{position:absolute;font-size:14px;font-weight:500}
.qty{position:absolute;display:flex;align-items:center;gap:6px;font-size:14px;font-weight:600}
.qty .plus{width:12px;height:12px;background:#111;color:#fff;font-size:11px;line-height:12px;text-align:center}
.qty .minus{width:12px;height:12px;border:1px solid #111;font-size:11px;line-height:9px;text-align:center}
.btn{position:absolute;background:var(--red);color:#fff;border-radius:6px;display:flex;align-items:center;justify-content:center;font-weight:600}
.heading{position:absolute;font-size:24px;font-weight:500;display:flex;align-items:center;gap:12px}
.field{position:absolute;height:47px;background:#fff;border-radius:3px;font-size:20px;color:#8a8a8a;padding-left:14px;display:flex;align-items:center}
.summary-row{position:absolute;left:777px;width:233px;display:flex;justify-content:space-between;font-size:21px;font-weight:500}
.summary-row b{color:var(--red);font-weight:500}
.featured{position:absolute;left:1097px;top:127px;width:275px;height:657px;background:var(--feature);border-radius:8px}
.featured-title{position:absolute;left:0;right:0;top:22px;text-align:center;font-size:28px;font-weight:500}
.card--feature .card-title{font-size:22px}
.card--feature .card-desc{font-size:11px;line-height:14px;left:10px;right:10px}
</style>
</head>
<body>
<div class="canvas">
<div class="stage">

<section class="screen screen--home">
  <aside class="sidebar">
    <div class="brand"><i></i>BASEPATH</div>
    <div class="nav-item is-active" style="top:150px">
      <svg viewBox="0 0 24 24"><path fill="currentColor" d="M12 3 2 12h3v9h5v-6h4v6h5v-9h3z"/></svg>Home
    </div>
    <div class="nav-item" style="top:226px"><svg viewBox="0 0 24 24"><path fill="currentColor" d="M2 4h3l3 11h11l2-8H7l-.6-3H2zm7 14a1.5 1.5 0 1 0 0 3 1.5 1.5 0 0 0 0-3zm8 0a1.5 1.5 0 1 0 0 3 1.5 1.5 0 0 0 0-3z"/></svg></div>
    <div class="nav-item" style="top:300px"><svg viewBox="0 0 24 24"><path fill="currentColor" d="M12 2 3 7l9 5 9-5zm-9 7v9l8 4v-9zm18 0-8 4v9l8-4z"/></svg></div>
    <div class="nav-item" style="top:380px"><svg viewBox="0 0 24 24"><path fill="none" stroke="currentColor" stroke-width="2.4" d="M4 15v-3a8 8 0 0 1 16 0v3"/><rect x="3" y="13" width="4" height="6" rx="1" fill="currentColor"/><rect x="17" y="13" width="4" height="6" rx="1" fill="currentColor"/></svg></div>
  </aside>
  <header class="topbar">
    <div class="search"><svg viewBox="0 0 24 24"><circle cx="10" cy="10" r="7" fill="none" stroke="#555" stroke-width="2"/><path d="m15 15 6 6" stroke="#555" stroke-width="2"/></svg>Search</div>
    <svg class="icon" style="left:1080px;top:20px;width:30px;height:32px" viewBox="0 0 24 24"><circle cx="12" cy="7" r="5" fill="#fff"/><path d="M3 22c0-6 4-8 9-8s9 2 9 8z" fill="#fff"/></svg>
    <svg class="icon" style="left:1138px;top:20px;width:36px;height:32px" viewBox="0 0 24 24"><path fill="#fff" d="M1 3h3l3 12h12l3-9H6.5L6 3zM9 18a2 2 0 1 0 0 4 2 2 0 0 0 0-4zm9 0a2 2 0 1 0 0 4 2 2 0 0 0 0-4z"/></svg>
    <div class="badge" style="left:1163px;top:17px">2</div>
  </header>

  <div class="photo photo--banner" role="img" aria-label="Banner photo of baseball players in a stadium"></div>
  <div class="photo photo--side" role="img" aria-label="Photo of a batter swinging under stadium lights"></div>

  <div class="dropdown">Wild Marlin
    <svg viewBox="0 0 26 22"><path d="M3 6l10 10L23 6" fill="none" stroke="#fff" stroke-width="3"/></svg>
  </div>

  <div class="card card--home" style="left:166px">
    <div class="prod prod--cap" style="top:28px;width:122px;height:150px" role="img" aria-label="Navy trucker hat"></div>
    <div class="card-title" style="top:196px">Wild Marlin Logo Hat</div>
    <div class="card-desc" style="top:232px">Step out in style in the marlin hat<br>- Wild Marlin logo in front</div>
    <div class="price">12.000 KD</div>
  </div>
  <div class="card card--home" style="left:476px">
    <div class="prod prod--tee" style="top:18px;width:140px;height:154px" role="img" aria-label="Grey printed t-shirt"></div>
    <div class="card-title" style="top:184px">Delta Flyway</div>
    <div class="card-desc" style="top:220px">If you don't have one yourself, you know someone with labrador.<br>The Delta flyway tee log features:</div>
    <div class="price">19.000 KD</div>
  </div>
  <div class="card card--home" style="left:786px">
    <div class="prod prod--hat" style="top:38px;width:136px;height:110px" role="img" aria-label="Blue patterned boonie hat"></div>
    <div class="card-title" style="top:198px">Reef Boonie Hat</div>
    <div class="card-desc" style="top:234px">The Reef Boonie hat can handle whatever your day has in store for you.</div>
    <div class="price">20.000 KD</div>
  </div>

  <div class="pager" style="left:563px;top:772px"><svg viewBox="0 0 16 18"><path d="M11 2 4 9l7 7" fill="none" stroke="#111" stroke-width="2.5"/></svg></div>
  <div class="pager" style="left:625px;top:772px"><svg viewBox="0 0 16 18"><path d="M5 2l7 7-7 7" fill="none" stroke="#111" stroke-width="2.5"/></svg></div>

  <div class="panel-title" style="left:1112px;top:422px">Shopping Cart
    <svg width="20" height="18" viewBox="0 0 24 24"><path fill="#111" d="M1 3h3l3 12h12l3-9H6.5L6 3zM9 18a2 2 0 1 0 0 4 2 2 0 0 0 0-4zm9 0a2 2 0 1 0 0 4 2 2 0 0 0 0-4z"/></svg></div>
  <div class="abs" style="left:1310px;top:426px;color:var(--red);font-size:17px;display:flex;gap:6px;align-items:center">Clear
    <svg width="14" height="16" viewBox="0 0 14 16"><path fill="#a5102c" d="M1 3h12v2H1zM5 1h4v2H5zM2 6h10l-1 10H3z"/></svg></div>
  <div class="rule" style="left:1112px;top:461px;width:250px"></div>
  <div class="rule" style="left:1112px;top:554px;width:250px"></div>
  <div class="rule" style="left:1112px;top:650px;width:250px"></div>

  <div class="thumb" style="left:1112px;top:478px"><span class="prod--cap" style="border-radius:14px 14px 5px 5px"></span></div>
  <div class="mini-name" style="left:1184px;top:486px">Wild Marlin Logo Hat</div>
  <div class="mini-price" style="left:1184px;top:510px">12.000 KD</div>
  <div class="qty" style="left:1311px;top:500px"><span class="plus">+</span>01<span class="minus">-</span></div>

  <div class="thumb" style="left:1112px;top:572px"><span class="prod--tee"></span></div>
  <div class="mini-name" style="left:1184px;top:580px">Delta Flyway</div>
  <div class="mini-price" style="left:1184px;top:604px">19.000 KD</div>
  <div class="qty" style="left:1311px;top:594px"><span class="plus">+</span>01<span class="minus">-</span></div>

  <div class="thumb" style="left:1112px;top:672px"><span class="prod--hat" style="top:14px;height:32px"></span></div>
  <div class="mini-name" style="left:1182px;top:677px">Reef Boonie Hat</div>
  <div class="mini-price" style="left:1184px;top:703px">20.000 KD</div>
  <div class="qty" style="left:1311px;top:694px"><span class="plus">+</span>01<span class="minus">-</span></div>

  <div class="abs" style="left:1112px;top:768px;font-size:25px;font-weight:500">51.000 KD</div>
  <div class="btn" style="left:1221px;top:762px;width:145px;height:44px;font-size:20px">Proceed to Buy</div>
</section>

<section class="screen screen--checkout">
  <aside class="sidebar">
    <div class="brand"><i></i>BASEPATH</div>
    <div class="nav-item" style="top:148px"><svg viewBox="0 0 24 24"><path fill="currentColor" d="M12 3 2 12h3v9h5v-6h4v6h5v-9h3z"/></svg></div>
    <div class="nav-item is-active" style="top:225px">
      <svg viewBox="0 0 24 24"><path fill="currentColor" d="M1 3h3l3 12h12l3-9H6.5L6 3zM9 18a2 2 0 1 0 0 4 2 2 0 0 0 0-4zm9 0a2 2 0 1 0 0 4 2 2 0 0 0 0-4z"/></svg>Cart
    </div>
    <div class="nav-item" style="top:298px"><svg viewBox="0 0 24 24"><path fill="currentColor" d="M12 2 3 7l9 5 9-5zm-9 7v9l8 4v-9zm18 0-8 4v9l8-4z"/></svg></div>
    <div class="nav-item" style="top:380px"><svg viewBox="0 0 24 24"><path fill="none" stroke="currentColor" stroke-width="2.4" d="M4 15v-3a8 8 0 0 1 16 0v3"/><rect x="3" y="13" width="4" height="6" rx="1" fill="currentColor"/><rect x="17" y="13" width="4" height="6" rx="1" fill="currentColor"/></svg></div>
  </aside>
  <header class="topbar">
    <div class="abs" style="left:24px;top:14px;color:#fff;font-size:32px;display:flex;align-items:center;gap:14px">
      <svg width="28" height="22" viewBox="0 0 28 22"><path d="M26 11H3M11 2 2 11l9 9" fill="none" stroke="#fff" stroke-width="2.4"/></svg>Checkout</div>
    <div class="search"><svg viewBox="0 0 24 24"><circle cx="10" cy="10" r="7" fill="none" stroke="#555" stroke-width="2"/><path d="m15 15 6 6" stroke="#555" stroke-width="2"/></svg>Search</div>
    <svg class="icon" style="left:1148px;top:18px;width:30px;height:32px" viewBox="0 0 24 24"><circle cx="12" cy="7" r="5" fill="#fff"/><path d="M3 22c0-6 4-8 9-8s9 2 9 8z" fill="#fff"/></svg>
  </header>

  <div class="heading" style="left:202px;top:100px">Order Details
    <svg width="20" height="18" viewBox="0 0 24 24"><path fill="#111" d="M1 3h3l3 12h12l3-9H6.5L6 3zM9 18a2 2 0 1 0 0 4 2 2 0 0 0 0-4zm9 0a2 2 0 1 0 0 4 2 2 0 0 0 0-4z"/></svg></div>
  <div class="rule" style="left:200px;top:139px;width:868px"></div>

  <div class="thumb" style="left:199px;top:154px"><span class="prod--cap" style="border-radius:14px 14px 5px 5px"></span></div>
  <div class="mini-name" style="left:270px;top:163px">Wild Marlin Logo Hat</div>
  <div class="mini-price" style="left:270px;top:187px">12.000 KD</div>
  <div class="qty" style="left:398px;top:178px"><span class="plus">+</span>01<span class="minus">-</span></div>

  <div class="thumb" style="left:493px;top:152px"><span class="prod--tee"></span></div>
  <div class="mini-name" style="left:565px;top:161px">Delta Flyway</div>
  <div class="mini-price" style="left:565px;top:184px">19.000 KD</div>
  <div class="qty" style="left:692px;top:175px"><span class="plus">+</span>01<span class="minus">-</span></div>

  <div class="thumb" style="left:787px;top:150px"><span class="prod--hat" style="top:14px;height:32px"></span></div>
  <div class="mini-name" style="left:858px;top:155px">Reef Boonie Hat</div>
  <div class="mini-price" style="left:858px;top:181px">20.000 KD</div>
  <div class="qty" style="left:986px;top:172px"><span class="plus">+</span>01<span class="minus">-</span></div>

  <div class="abs" style="left:200px;top:248px;font-size:25px;font-weight:500">Total &nbsp;: &nbsp;51.000 KD</div>
  <div class="rule" style="left:200px;top:302px;width:868px"></div>

  <div class="heading" style="left:202px;top:316px;font-size:23px">Deliver To</div>
  <div class="field" style="left:202px;top:359px;width:240px">First Name*</div>
  <div class="field" style="left:467px;top:359px;width:240px">Last Name*</div>
  <div class="field" style="left:202px;top:425px;width:505px">Phone*</div>
  <div class="field" style="left:202px;top:488px;width:505px">Area*</div>
  <div class="field" style="left:202px;top:551px;width:240px">Block*</div>
  <div class="field" style="left:467px;top:551px;width:240px">Street *</div>
  <div class="field" style="left:202px;top:615px;width:240px">Avenue</div>
  <div class="field" style="left:467px;top:615px;width:240px">Building</div>
  <div class="field" style="left:202px;top:675px;width:240px">Floor</div>
  <div class="field" style="left:467px;top:675px;width:240px">Appartment</div>
  <div class="field" style="left:202px;top:737px;width:505px">Map Location</div>

  <div class="summary-row" style="top:355px">Sub Total<b>51.000 KD</b></div>
  <div class="summary-row" style="top:385px">Delivery Charge<b>5.000 KD</b></div>
  <div class="summary-row" style="top:415px">Total<b>56.000 KD</b></div>

  <div class="heading" style="left:778px;top:476px;font-size:21px">Payment Method</div>
  <div class="abs" style="left:780px;top:513px;width:31px;height:31px;background:#fff;border-radius:3px"></div>
  <div class="abs" style="left:825px;top:516px;font-size:20px">Netpay Card</div>

  <div class="heading" style="left:778px;top:569px;font-size:21px">Discount Coupon</div>
  <div class="field" style="left:780px;top:610px;width:169px;height:46px;color:#333;padding-left:16px">Coupon Code</div>
  <div class="btn" style="left:960px;top:610px;width:84px;height:44px;font-size:21px">Apply</div>
  <div class="btn" style="left:780px;top:683px;width:265px;height:48px;font-size:22px">Place Order</div>

  <div class="featured">
    <div class="featured-title">Featured Products</div>
    <div class="card card--feature" style="left:32px;top:75px;width:214px;height:265px">
      <div class="prod prod--cap" style="top:18px;width:92px;height:112px" role="img" aria-label="Navy trucker hat"></div>
      <div class="card-title" style="top:142px">Wild Marlin Logo Hat</div>
      <div class="card-desc" style="top:174px">Step out in style in the marlin hat<br>- Wild Marlin logo in front</div>
      <div class="price" style="left:11px;right:12px;top:214px;height:36px;font-size:22px">12.000 KD</div>
    </div>
    <div class="card card--feature" style="left:33px;top:375px;width:211px;height:261px">
      <div class="prod prod--tee" style="top:14px;width:130px;height:112px" role="img" aria-label="Grey printed t-shirt"></div>
      <div class="card-title" style="top:130px">Delta Flyway</div>
      <div class="card-desc" style="top:162px">If you don't have one yourself, you know someone with labrador.<br>The Delta flyway tee log features:</div>
      <div class="price" style="left:11px;right:11px;top:211px;height:36px;font-size:22px">19.000 KD</div>
    </div>
  </div>
</section>

</div>
</div>
</body>
</html>
```